BrimFalcon Business Cards

We have a defined brand. Please visit our website to get a feel for the product and the color pallets. www.brimfalcon-example.com

We need an updated, world class business card design. (See the attached existing card design). Please utilize BOTH sides of the card as shown and be creative with the layout. I do want the horse head icon to be positioned as it is with the existing card.

The remainder of the layout can be customized and I also want it vertically oriented.

Attached are the logo files and please use the colors as follows:
Green - #A5CE39
Tan - #CDBD99
Black

Feel free to play with the colors.

```html
<!DOCTYPE html>
<html lang="en">
<head>
<meta charset="utf-8">
<title>BrimFalcon Business Cards</title>
<link href="https://fonts.googleapis.com/css2?family=Michroma&family=Open+Sans:wght@400;600;700&display=swap" rel="stylesheet">
<style>
  :root {
    --stage: #1f1f1f;
    --green-deep: #3a9448;
    --green-brand: #A5CE39;
    --lime-glow: #c9d92a;
    --ink: #111111;
    --text: #2b2b2b;
    --paper: #ffffff;
  }
  * { margin: 0; padding: 0; box-sizing: border-box; }
  html, body { width: 1200px; height: 900px; overflow: hidden; }
  body {
    background: var(--stage);
    font-family: "Open Sans", sans-serif;
    position: relative;
  }
  .card {
    position: absolute;
    top: 135px;
    width: 360px;
    height: 630px;
    border-radius: 24px;
    overflow: hidden;
  }
  /* Front side */
  .card-front {
    left: 210px;
    background: radial-gradient(ellipse at 55% 45%, var(--lime-glow) 0%, var(--green-brand) 32%, var(--green-deep) 88%);
    display: flex;
    align-items: center;
    justify-content: center;
  }
  .front-mark {
    display: flex;
    flex-direction: column;
    align-items: center;
    gap: 20px;
  }
  .front-mark .dot {
    width: 96px; height: 96px;
    border-radius: 50%;
    background: var(--ink);
  }
  .front-mark .name {
    font-weight: 700;
    font-size: 44px;
    color: var(--ink);
    letter-spacing: 0.5px;
    line-height: 1;
  }
  /* Back side */
  .card-back {
    left: 630px;
    background: var(--paper);
  }
  .brand {
    position: absolute;
    left: 30px;
    top: 64px;
    display: flex;
    align-items: center;
    gap: 12px;
  }
  .brand .dot {
    width: 44px; height: 44px;
    border-radius: 50%;
    background: var(--ink);
    flex: none;
  }
  .brand .wordmark {
    font-weight: 700;
    font-size: 26px;
    color: var(--ink);
    line-height: 1;
  }
  .brand .tagline {
    font-weight: 600;
    font-size: 11px;
    letter-spacing: 2.6px;
    color: var(--ink);
    margin-top: 7px;
  }
  .person {
    position: absolute;
    left: 40px;
    top: 196px;
  }
  .person .name {
    font-family: "Michroma", sans-serif;
    font-size: 17px;
    letter-spacing: 3px;
    color: var(--green-brand);
  }
  .person .role {
    font-size: 11px;
    color: var(--text);
    margin-top: 3px;
  }
  .contacts {
    position: absolute;
    left: 40px;
    top: 276px;
    list-style: none;
  }
  .contacts li {
    display: flex;
    align-items: center;
    gap: 10px;
    font-size: 11px;
    color: var(--text);
    line-height: 1.3;
    margin-bottom: 9px;
  }
  .contacts svg { width: 22px; height: 22px; flex: none; }
  .stripe-glow {
    position: absolute;
    left: 0; right: 0;
    top: 520px; height: 20px;
    background: linear-gradient(90deg, var(--green-deep), var(--lime-glow) 45%, var(--green-brand) 70%, var(--green-deep));
  }
  .stripe-solid {
    position: absolute;
    left: 0; right: 0;
    top: 558px; height: 26px;
    background: var(--green-deep);
  }
</style>
</head>
<body>
  <section class="card card-front">
    <div class="front-mark">
      <span class="dot"></span>
      <span class="name">BrimFalcon</span>
    </div>
  </section>

  <section class="card card-back">
    <div class="brand">
      <span class="dot"></span>
      <div>
        <div class="wordmark">BrimFalcon Labs</div>
        <div class="tagline">Performance Driven EVs</div>
      </div>
    </div>

    <div class="person">
      <div class="name">DANIEL REYES</div>
      <div class="role">CEO/Managing Director</div>
    </div>

    <ul class="contacts">
      <li>
        <svg viewBox="0 0 22 22"><circle cx="11" cy="11" r="11" fill="#111"/><path d="M7.5 6c.6-.4 1.2-.3 1.5.2l1 1.6c.3.5.2 1-.2 1.3l-.6.5c.5 1.2 1.3 2 2.5 2.6l.5-.6c.3-.4.9-.5 1.3-.2l1.6 1c.5.3.6 1 .2 1.5-.7.9-1.700 1.2-2.7.8-2.6-1-4.4-2.8-5.4-5.4-.4-1 0-2 .3-2.3z" fill="#fff"/></svg>
        555-010-4821
      </li>
      <li>
        <svg viewBox="0 0 22 22"><circle cx="11" cy="11" r="11" fill="#111"/><path d="M5.5 11 11 6l5.5 5M7.5 10v5.5h7V10" fill="none" stroke="#fff" stroke-width="1.4"/></svg>
        555-010-4821
      </li>
      <li>
        <svg viewBox="0 0 22 22"><circle cx="11" cy="11" r="11" fill="#111"/><rect x="5.5" y="7.5" width="11" height="7.5" fill="none" stroke="#fff" stroke-width="1.2"/><path d="M5.5 7.5 11 12l5.5-4.5" fill="none" stroke="#fff" stroke-width="1.2"/></svg>
        dreyes@brimfalcon-example.com
      </li>
      <li>
        <svg viewBox="0 0 22 22"><circle cx="11" cy="11" r="11" fill="#111"/><path d="M11 17s-4-4.3-4-7.2a4 4 0 0 1 8 0C15 12.7 11 17 11 17z" fill="#fff"/><circle cx="11" cy="9.8" r="1.5" fill="#111"/></svg>
        <span>118 Harlow Street NE<br>Suite 210, Fairview MI 49000</span>
      </li>
    </ul>

    <div class="stripe-glow"></div>
    <div class="stripe-solid"></div>
  </section>
</body>
</html>
```